Ferncourt Labour Walk 2013

I am seeking to create a flyer promoting the event May Day in Sydney. The Event is a March and will be taking place on the 5th May Sunday. The Projection of the flyer should be fresh and modern but capable of encapsulating values of struggle, justice and solidarity. It is an event that started in the late 1800's in a struggle to obtain the 8 hour day.
This flyer should capture the old logo with a fresh modern interpretation.
Updates

HI All, 

Can we add the following details to design. Apologies it came late, it just got forwarded onto me. 

Twitter (logo) @FerncourtLabour
Facebook (logo) Labour Ferncourt 2013

Thanks

Reason: I want to allow designers the opportunity to make revisions on their existing designs.

Reason: Last minute changes are not coming through.

Target Market(s)

General Public, Union Members, Workers, advocates of social justice and democracy

Industry/Entity Type

Event

Requirements
Must have
• Event Details:
Ferncourt Labour Walk
Sunday May 5th
Assembling: 11:30am
Marching: 12:00pm
Assembly Point: Tindale Street outside Corvell Hall, Sydney
Ferncourt Labour Logo (See Attachment) This logo should be manipulated to show a fresh and modern aspect to it, whilst retaing the same characteristics.

Nice to have
• Themes of the flyer should capture the following ideas:
International Workers Solidarity
Workers Rights
Fight for the 8 hour day
location being Sydney Australia
Images of
People Rallying, protesting, marching

```html
<!DOCTYPE html>
<html lang="en">
<head>
<meta charset="utf-8">
<title>Ferncourt Labour Walk 2013</title>
<link rel="stylesheet" href="https://fonts.googleapis.com/css2?family=Archivo+Black&family=Permanent+Marker&display=block">
<style>
  :root {
    --paper: #ffffff;
    --march-red: #ee2a2e;
    --ink: #0d0d0d;
    --type-light: #ffffff;
  }
  html, body {
    margin: 0;
    padding: 0;
    width: 927px;
    height: 1200px;
    overflow: hidden;
    background: var(--paper);
  }
  .flyer {
    position: relative;
    width: 927px;
    height: 1200px;
    overflow: hidden;
    background: var(--paper);
  }
  .event-title {
    position: absolute;
    left: 56px;
    top: 70px;
    width: 780px;
    margin: 0;
    font-family: "Permanent Marker", "Archivo Black", sans-serif;
    font-weight: 400;
    color: var(--march-red);
    line-height: 1;
    text-transform: uppercase;
    transform: rotate(-5deg);
    transform-origin: left top;
    white-space: nowrap;
  }
  .event-title span { display: block; }
  .event-title .line-one { font-size: 104px; height: 150px; }
  .event-title .line-two { font-size: 150px; height: 190px; padding-left: 60px; }
  .event-title .line-three { font-size: 190px; padding-left: 70px; }
  .crowd {
    position: absolute;
    left: 0;
    top: 620px;
    width: 927px;
    height: 200px;
  }
  .organiser {
    position: absolute;
    right: 34px;
    top: 583px;
    display: flex;
    align-items: center;
    gap: 16px;
  }
  .organiser-name {
    font-family: "Archivo Black", sans-serif;
    font-size: 20px;
    line-height: 1.15;
    color: var(--march-red);
    text-align: right;
    text-transform: uppercase;
    margin-top: -60px;
  }
  .organiser-mark {
    width: 190px;
    height: 190px;
    border-radius: 50%;
    background: var(--march-red);
  }
  .details-band {
    position: absolute;
    left: 0;
    top: 818px;
    width: 927px;
    height: 382px;
    background: var(--ink);
  }
  .event-details {
    position: absolute;
    left: 0;
    top: 868px;
    width: 927px;
    margin: 0;
    font-family: "Archivo Black", sans-serif;
    font-size: 55px;
    line-height: 60px;
    color: var(--type-light);
    text-align: center;
    text-transform: uppercase;
  }
  .event-details span { display: block; }
</style>
</head>
<body>
  <main class="flyer">
    <h1 class="event-title">
      <span class="line-one">Ferncourt</span>
      <span class="line-two">Labour</span>
      <span class="line-three">Walk</span>
    </h1>

    <svg class="crowd" viewBox="0 0 927 200" preserveAspectRatio="none" role="img" aria-label="Silhouetted crowd of marchers raising fists and waving flags">
      <defs>
        <linearGradient id="crowd-fade" x1="0" y1="0" x2="0" y2="1">
          <stop offset="0" stop-color="#0d0d0d" stop-opacity="0"/>
          <stop offset="0.5" stop-color="#0d0d0d" stop-opacity="0.7"/>
          <stop offset="1" stop-color="#0d0d0d"/>
        </linearGradient>
      </defs>
      <rect x="0" y="0" width="927" height="200" fill="url(#crowd-fade)"/>
    </svg>

    <div class="organiser">
      <div class="organiser-name">Ferncourt Labour<br>Committee</div>
      <div class="organiser-mark"></div>
    </div>

    <div class="details-band"></div>
    <p class="event-details">
      <span>Sunday, May 5th, 2013</span>
      <span>12:00PM</span>
      <span>Tindale Street</span>
      <span>Outside Corvell</span>
      <span>Hall Sydney</span>
    </p>
  </main>
</body>
</html>
```